Investor Slide Deck

Simple idea - take a model investor deck and build out a investor deck for K7V. I will complete the data, I need a template to work from within. I will attach a model investor deck and a blank K7V that I need built out to K7V. Use the K7V Pwrpt to build out the investor deck

```html
<!DOCTYPE html>
<html lang="en">
<head>
<meta charset="utf-8">
<title>K7V Waypoint Career – Investor Deck Template</title>
<link href="https://fonts.googleapis.com/css2?family=Outfit:wght@300;400;500;600;700;800&display=swap" rel="stylesheet">
<style>
:root{
  --board:#8ca9d4;
  --navy:#0c3550;
  --navy-deep:#0a2a44;
  --teal:#0aa89c;
  --orange:#fa5510;
  --yellow:#f8b92b;
  --ink:#222a30;
  --muted:#5a6168;
  --line:#e8ecef;
  --soft:#f2f3f4;
}
*{box-sizing:border-box;margin:0;padding:0}
html,body{width:1200px;height:1097px;overflow:hidden}
body{background:var(--board);font-family:"Outfit",sans-serif;color:var(--ink);position:relative}
.slide{position:absolute;overflow:hidden;background:#fff;box-shadow:0 10px 14px -8px rgba(20,40,70,.55)}
.abs{position:absolute}
.dark{background:radial-gradient(ellipse at 35% 25%,#0e5a6a 0%,var(--navy) 45%,var(--navy-deep) 100%);color:#fff}
.label{font-size:7.5px;font-weight:600;color:var(--orange);letter-spacing:.1px}
.heading{font-size:15px;font-weight:500;color:var(--ink);line-height:1.1}
.rule{display:block;width:16px;height:1.5px;background:var(--teal);margin-top:4px}
.body{font-size:5.2px;line-height:1.4;color:var(--muted);font-weight:300}
.lead{font-size:6.2px;line-height:1.35;color:var(--ink);font-weight:400}
.card{position:absolute;background:#fff;border:.8px solid var(--line);border-radius:3px;padding:4px 5px;box-shadow:0 1px 3px rgba(0,0,0,.06);overflow:hidden}
.card h4{font-size:6px;font-weight:500;line-height:1.15}
.card h5{font-size:6px;font-weight:500;color:var(--ink);line-height:1.15;margin-bottom:2px}
.c-orange{color:var(--orange)}.c-teal{color:var(--teal)}.c-yellow{color:var(--yellow)}
.b-orange{border-color:#fbd3c2}.b-teal{border-color:#bfe6e2}.b-yellow{border-color:#fbe6b6}
.photo{position:absolute}
.brand{display:flex;align-items:center;gap:7px;color:#fff;font-weight:600}
.brand .mark{background:var(--orange)}
.band{position:absolute}
</style>
</head>
<body>

<!-- Cover -->
<section class="slide dark" style="left:298px;top:43px;width:602px;height:339px">
  <div class="abs brand" style="left:0;right:0;top:58px;justify-content:center;font-size:20px;letter-spacing:.3px">
    <span class="mark" style="width:14px;height:14px"></span>K7V&nbsp;&nbsp;WAYPOINT CAREERS
  </div>
  <h1 class="abs" style="left:0;right:0;top:152px;text-align:center;font-size:44px;font-weight:800;letter-spacing:-.5px;line-height:1">WAYPOINT CAREER</h1>
  <div class="abs" style="left:0;right:0;top:222px;display:flex;justify-content:center;align-items:center;gap:10px;font-size:21px;font-weight:400">
    <span style="width:36px;height:1px;background:var(--orange)"></span><span style="letter-spacing:8px;margin-right:-8px">2024</span><span style="width:36px;height:1px;background:var(--orange)"></span>
  </div>
  <div class="abs" style="left:0;right:0;top:245px;text-align:center;font-size:34px;font-weight:400;color:var(--yellow);line-height:1.1">Investor Deck</div>
</section>

<!-- Introduction -->
<section class="slide" style="left:45px;top:408px;width:356px;height:200px">
  <div class="abs" style="left:21px;top:46px">
    <div class="label">WAYPOINT CAREER</div>
    <div class="heading" style="margin-top:3px">Introduction</div>
    <span class="rule"></span>
    <p class="lead" style="margin-top:6px;font-size:7.6px;line-height:1.2">
      <span class="c-orange">Career-connected</span> learning thrives<br>in <span class="c-teal">career-connected communities.</span></p>
    <p class="body" style="margin-top:6px;width:120px;font-size:5.8px">Waypoint Careers™ (K7V) solves some of the biggest challenges in education, helping learners and teachers make daily connections between what they’re doing now in the classroom and what they’ll do later in life.</p>
  </div>
  <div class="band" style="left:178px;top:78px;width:8px;height:110px;background:var(--orange);border-radius:4px"></div>
  <div class="photo" role="img" aria-label="Portrait of a smiling professional holding a tablet and pen" style="left:200px;top:14px;width:130px;height:174px;border-radius:8px;background:linear-gradient(180deg,#efe8e2 0%,#c9b6a4 35%,#2a2a2e 70%,#1a1a1c 100%)"></div>
</section>

<!-- Problems -->
<section class="slide" style="left:421px;top:408px;width:356px;height:200px">
  <div class="abs" style="left:22px;top:41px">
    <div class="label">WAYPOINT CAREER</div>
    <div class="heading" style="margin-top:3px">Problems</div>
    <span class="rule"></span>
    <p class="lead" style="margin-top:8px;width:108px">Lorem ipsum dolor sit amet, consectetur adipiscing elit, sed do eiusmod tempor incididunt</p>
    <p class="body" style="margin-top:5px;width:108px">Lorem ipsum dolor sit amet, consectetur adipiscing elit, sed do eiusmod tempor incididunt ut labore et dolore magna aliqua. Lorem ipsum dolor sit amet, consectetur adipiscing elit, sed do eiusmod tempor incididunt ut labore et dolore magna aliqua.</p>
  </div>
  <div class="card b-orange" style="left:149px;top:37px;width:89px;height:60px"><h4 class="c-orange">Lorem Ipsum</h4><h5>Dolor Sit Amet</h5><p class="body">Lorem ipsum dolor sit amet, consectetur adipiscing elit, sed do eiusmod tempor incididunt ut labore et dolore</p></div>
  <div class="card b-yellow" style="left:245px;top:37px;width:89px;height:60px"><h4 class="c-yellow">Lorem Ipsum</h4><h5>Dolor Sit Amet</h5><p class="body">Lorem ipsum dolor sit amet, consectetur adipiscing elit, sed do eiusmod tempor incididunt ut labore et dolore</p></div>
  <div class="card b-teal" style="left:142px;top:104px;width:89px;height:60px"><h4 class="c-teal">Lorem Ipsum</h4><h5>Dolor Sit Amet</h5><p class="body">Lorem ipsum dolor sit amet, consectetur adipiscing elit, sed do eiusmod tempor incididunt ut labore et dolore</p></div>
  <div class="card b-orange" style="left:238px;top:104px;width:89px;height:60px"><h4 class="c-orange">Lorem Ipsum</h4><h5>Dolor Sit Amet</h5><p class="body">Lorem ipsum dolor sit amet, consectetur adipiscing elit, sed do eiusmod tempor incididunt ut labore et dolore</p></div>
</section>

<!-- Solutions -->
<section class="slide" style="left:798px;top:408px;width:356px;height:200px">
  <div class="abs" style="left:22px;top:20px">
    <div class="label">WAYPOINT CAREER</div>
    <div class="heading" style="margin-top:3px">Solutions</div>
    <span class="rule"></span>
  </div>
  <div class="card b-teal" style="left:17px;top:56px;width:94px;height:41px"><h4 class="c-teal">Lorem Ipsum</h4><p class="body">Lorem ipsum dolor sit amet, consectetur adipiscing elit, sed do eiusmod tempor incididunt</p></div>
  <div class="card" style="left:127px;top:56px;width:94px;height:41px;border-color:transparent;box-shadow:none"><h4 style="color:#1b6a86">Lorem Ipsum</h4><p class="body">Lorem ipsum dolor sit amet, consectetur adipiscing elit, sed do eiusmod tempor incididunt</p></div>
  <div class="card" style="left:17px;top:100px;width:94px;height:41px;border-color:transparent;box-shadow:none"><h4 style="color:#1b6a86">Lorem Ipsum</h4><p class="body">Lorem ipsum dolor sit amet, consectetur adipiscing elit, sed do eiusmod tempor incididunt</p></div>
  <div class="card b-yellow" style="left:127px;top:100px;width:94px;height:41px"><h4 class="c-yellow">Lorem Ipsum</h4><p class="body">Lorem ipsum dolor sit amet, consectetur adipiscing elit, sed do eiusmod tempor incididunt</p></div>
  <div class="card b-orange" style="left:17px;top:144px;width:94px;height:41px"><h4 class="c-orange">Lorem Ipsum</h4><p class="body">Lorem ipsum dolor sit amet, consectetur adipiscing elit, sed do eiusmod tempor incididunt</p></div>
  <div class="card" style="left:127px;top:144px;width:94px;height:41px;border-color:transparent;box-shadow:none"><h4 style="color:#1b6a86">Lorem Ipsum</h4><p class="body">Lorem ipsum dolor sit amet, consectetur adipiscing elit, sed do eiusmod tempor incididunt</p></div>
  <div class="photo" role="img" aria-label="Glowing light bulb resting on an open hand" style="left:232px;top:18px;width:124px;height:176px;border-radius:6px 0 0 6px;background:radial-gradient(circle at 45% 28%,#f7c77a 0%,#b8b0a4 22%,#6d6d6d 55%,#2e2e2e 100%)"></div>
</section>

<!-- Core Values -->
<section class="slide" style="left:45px;top:629px;width:356px;height:200px">
  <div class="abs" style="left:21px;top:19px">
    <div class="label">WAYPOINT CAREER</div>
    <div class="heading" style="margin-top:3px">Core Values</div>
    <span class="rule"></span>
  </div>
  <div class="card b-teal" style="left:31px;top:62px;width:108px;height:37px"><h5>Quality</h5><p class="body">Lorem ipsum dolor sit amet, consectetur adipiscing elit, sed do eiusmod tempor incididunt ut labore et dolore</p></div>
  <div class="card b-teal" style="left:31px;top:105px;width:108px;height:37px"><h5>Satisfaction</h5><p class="body">Lorem ipsum dolor sit amet, consectetur adipiscing elit, sed do eiusmod tempor incididunt ut labore et dolore</p></div>
  <div class="card b-teal" style="left:31px;top:148px;width:108px;height:37px"><h5>Ethics</h5><p class="body">Lorem ipsum dolor sit amet, consectetur adipiscing elit, sed do eiusmod tempor incididunt ut labore et dolore</p></div>
  <div class="card" style="left:219px;top:29px;width:101px;height:70px;background:var(--orange);border:0;color:#fff"><h4 style="font-size:8px">Mission</h4><p class="body" style="color:#ffe3d6;margin-top:2px">Lorem ipsum dolor sit amet, consectetur adipiscing elit, sed do eiusmod tempor incididunt ut labore et dolore magna aliqua. Lorem ipsum dolor sit amet, consectetur</p></div>
  <div class="card" style="left:135px;top:91px;width:92px;height:67px;background:var(--teal);border:0;color:#fff"><h4 style="font-size:8px">Values</h4><p class="body" style="color:#dcf5f2;margin-top:2px">Lorem ipsum dolor sit amet, consectetur adipiscing elit, sed do eiusmod tempor incididunt ut labore et dolore magna aliqua. Lorem ipsum dolor sit amet</p></div>
  <div class="card" style="left:234px;top:107px;width:101px;height:70px;background:var(--yellow);border:0;color:var(--ink)"><h4 style="font-size:8px">Vision</h4><p class="body" style="color:#4a3a10;margin-top:2px">Lorem ipsum dolor sit amet, consectetur adipiscing elit, sed do eiusmod tempor incidid ut labore et dolore magna aliqua. Lorem ipsum dolor sit amet, consectetur</p></div>
</section>

<!-- Section title -->
<section class="slide dark" style="left:421px;top:629px;width:356px;height:200px">
  <div class="abs" style="left:32px;top:78px">
    <div style="font-size:7.5px;letter-spacing:2px;color:var(--teal);font-weight:500">TITLE SLIDE</div>
    <div style="font-size:17px;font-weight:700;line-height:1;margin-top:4px">PROFESSIONAL</div>
    <div style="font-size:17px;font-weight:700;line-height:1;color:var(--orange)">DEVELOPMENT</div>
    <span style="display:block;width:40px;height:2px;background:var(--yellow);margin:5px 0 0 72px"></span>
  </div>
  <span class="abs" style="left:161px;top:76px;width:.8px;height:54px;background:rgba(255,255,255,.45)"></span>
  <p class="abs body" style="left:174px;top:79px;width:160px;color:#d7e2ea">Lorem ipsum dolor sit amet, consectetur adipiscing elit, sed do eiusmod tempor incididunt ut labore et dolore magna aliqua. Lorem ipsum dolor sit amet, consectetur adipiscing elit, sed do eiusmod tempor incididunt ut labore et dolore magna aliqua. Sed do eiusmod tempor incididunt ut labore et dolore magna aliqua.</p>
</section>

<!-- It doesn't stop -->
<section class="slide" style="left:798px;top:629px;width:356px;height:200px">
  <div class="abs" style="left:21px;top:46px">
    <div class="label">WAYPOINT CAREER</div>
    <div class="heading" style="margin-top:3px">It <span class="c-yellow">Doesn’t</span> <span class="c-orange">Stop</span> There</div>
    <span class="rule"></span>
    <p class="lead" style="margin-top:7px;width:135px;font-weight:500">Lorem ipsum dolor sit amet, consectetur adipiscing elit, sed do eiusmod tempor incididunt ut labore et dolore magna aliqua.</p>
    <p class="body" style="margin-top:5px;width:148px">Lorem ipsum dolor sit amet, consectetur adipiscing elit, sed do eiusmod tempor incididunt ut labore et dolore magna aliqua. Lorem ipsum dolor sit amet, consectetur adipiscing elit, sed do eiusmod tempor incididunt ut labore et dolore magna aliqua.</p>
  </div>
  <div class="photo" role="img" aria-label="Young plant growing from stacks of gold coins in a city at dusk" style="left:194px;top:22px;width:149px;height:99px;border-radius:3px;background:linear-gradient(160deg,#2e4e6e 0%,#6a7c8a 35%,#c08a3a 65%,#3a3020 100%)"></div>
  <div class="card" style="left:183px;top:116px;width:130px;height:56px;background:var(--orange);border:0"><p class="body" style="color:#fff">Lorem ipsum dolor sit amet, consectetur adipiscing elit, sed do eiusmod tempor incididunt ut labore et dolore magna aliqua. Lorem ipsum dolor sit amet, consectetur adipiscing elit, sed do eiusmod tempor incididunt ut labore et dolore magna aliqua.</p></div>
</section>

<!-- Annual overview -->
<section class="slide" style="left:45px;top:850px;width:356px;height:200px">
  <div class="band" style="left:0;top:0;width:356px;height:70px;background:var(--teal)"></div>
  <div class="band" style="left:0;top:70px;width:356px;height:1.5px;background:var(--yellow)"></div>
  <div class="abs" style="left:21px;top:26px;color:#fff">
    <div class="label">WAYPOINT CAREER</div>
    <div style="font-size:15px;font-weight:500;margin-top:4px;line-height:1.1">Annual Overview</div>
  </div>
  <p class="abs body" style="left:161px;top:22px;width:175px;color:#e3f7f4">Lorem ipsum dolor sit amet, consectetur adipiscing elit, sed do eiusmod tempor incididunt ut labore et dolore magna aliqua. Lorem ipsum dolor sit amet, consectetur adipiscing elit, sed do eiusmod tempor incididunt ut labore et dolore magna aliqua.</p>
  <svg class="abs" style="left:20px;top:100px" width="325" height="92" viewBox="0 0 325 92" font-family="Outfit,sans-serif" font-size="3.4" fill="#666">
    <g stroke="#eee" stroke-width=".4"><line x1="18" y1="4" x2="320" y2="4"/><line x1="18" y1="21" x2="320" y2="21"/><line x1="18" y1="39" x2="320" y2="39"/><line x1="18" y1="56" x2="320" y2="56"/><line x1="18" y1="74" x2="320" y2="74"/></g>
    <text x="4" y="5">70k</text><text x="4" y="22">60k</text><text x="4" y="40">40k</text><text x="4" y="57">20k</text><text x="4" y="75">0k</text>
    <g fill="#ddd">
      <rect x="22" y="67" width="11" height="7"/><rect x="45" y="63" width="11" height="11"/><rect x="68" y="50" width="11" height="24"/><rect x="91" y="6" width="11" height="68"/><rect x="114" y="38" width="11" height="36"/><rect x="137" y="44" width="11" height="30"/><rect x="160" y="62" width="11" height="12"/><rect x="183" y="38" width="11" height="36"/><rect x="206" y="50" width="11" height="24"/><rect x="229" y="61" width="11" height="13"/><rect x="252" y="35" width="11" height="39"/><rect x="275" y="14" width="11" height="60"/><rect x="298" y="44" width="11" height="30"/>
    </g>
    <g fill="var(--orange)">
      <rect x="22" y="69" width="11" height="5"/><rect x="45" y="66" width="11" height="8"/><rect x="68" y="52" width="11" height="22"/><rect x="91" y="14" width="11" height="60"/><rect x="114" y="47" width="11" height="27"/><rect x="137" y="50" width="11" height="24"/><rect x="160" y="63" width="11" height="11"/><rect x="183" y="47" width="11" height="27"/><rect x="206" y="54" width="11" height="20"/><rect x="229" y="65" width="11" height="9"/><rect x="252" y="52" width="11" height="22"/><rect x="275" y="22" width="11" height="52"/><rect x="298" y="52" width="11" height="22"/>
    </g>
    <g text-anchor="middle"><text x="27" y="81">2014</text><text x="50" y="81">2015</text><text x="73" y="81">2016</text><text x="96" y="81">2017</text><text x="119" y="81">2018</text><text x="142" y="81">2020</text><text x="165" y="81">2014</text><text x="188" y="81">2015</text><text x="211" y="81">2016</text><text x="234" y="81">2017</text><text x="257" y="81">2018</text><text x="280" y="81">2020</text><text x="303" y="81">2020</text></g>
  </svg>
</section>

<!-- Solutions with stats -->
<section class="slide" style="left:421px;top:850px;width:356px;height:200px">
  <div class="abs" style="left:0;top:0;width:143px;height:200px;background:var(--soft)"></div>
  <div class="abs" style="left:22px;top:38px">
    <div class="label">WAYPOINT CAREER</div>
    <div class="heading" style="margin-top:3px">Solutions</div>
    <span class="rule"></span>
    <p class="lead" style="margin-top:7px;width:110px">Lorem ipsum dolor sit amet, labore elit, sed do eiusmod tempor dolore incididunt ut labore et dolore amet magna aliqua.</p>
    <p class="body" style="margin-top:5px;width:110px">Lorem ipsum dolor sit amet, consectetur adipiscing elit, sed do eiusmod tempor incididunt ut labore et dolore magna aliqua. Sed do eiusmod tempor incididunt ut labore et dolore magna</p>
  </div>
  <div class="card b-orange" style="left:161px;top:24px;width:94px;height:56px"><h4 class="c-orange">Lorem Ipsum</h4><p class="body">Lorem ipsum dolor sit amet, consectetur adipiscing elit, sed do eiusmod tempor incididunt ut labore et dolore magna</p></div>
  <svg class="abs" style="left:268px;top:24px" width="60" height="76" font-family="Outfit,sans-serif">
    <circle cx="30" cy="30" r="24" fill="none" stroke="#cfd3d6" stroke-width="3"/>
    <path d="M30 6 A24 24 0 0 0 30 54" fill="none" stroke="var(--orange)" stroke-width="7"/>
    <text x="30" y="32" text-anchor="middle" font-size="6" font-weight="600" fill="#222">50%</text>
    <text x="30" y="71" text-anchor="middle" font-size="3.6" font-weight="500" fill="#333">Add Your Text One</text>
  </svg>
  <svg class="abs" style="left:160px;top:106px" width="60" height="76" font-family="Outfit,sans-serif">
    <circle cx="30" cy="30" r="24" fill="none" stroke="#cfd3d6" stroke-width="3"/>
    <path d="M30 6 A24 24 0 1 1 6 30" fill="none" stroke="var(--teal)" stroke-width="7"/>
    <text x="30" y="32" text-anchor="middle" font-size="6" font-weight="600" fill="#222">75%</text>
    <text x="30" y="71" text-anchor="middle" font-size="3.6" font-weight="500" fill="#333">Add Your Text Two</text>
  </svg>
  <div class="card b-teal" style="left:232px;top:116px;width:94px;height:56px"><h4 class="c-teal">Lorem Ipsum</h4><p class="body">Lorem ipsum dolor sit amet, consectetur adipiscing elit, sed do eiusmod tempor incididunt ut labore et dolore magna</p></div>
</section>

<!-- Thank you -->
<section class="slide dark" style="left:798px;top:850px;width:356px;height:200px;background:radial-gradient(ellipse at 40% 45%,#0b6478 0%,#0a4d64 50%,#0b3b55 100%)">
  <div class="abs brand" style="left:0;right:0;top:36px;justify-content:center;font-size:13px">
    <span class="mark" style="width:10px;height:10px"></span>K7V&nbsp;&nbsp;WAYPOINT CAREERS
  </div>
  <div class="abs" style="left:0;right:0;top:90px;text-align:center;font-size:34px;font-weight:700;line-height:1;letter-spacing:-.5px"><span class="c-yellow">Thank</span> <span class="c-orange">You!</span></div>
  <p class="abs body" style="left:88px;width:180px;top:144px;text-align:center;color:#d6e6ec">Lorem ipsum dolor sit amet, consectetur adipiscing elit, sed do eiusmod tempor incididunt ut labore et dolore magna aliqua. Sed do eiusmod tempor incididunt ut labore et dolore magna aliqua.</p>
</section>

</body>
</html>
```